Business Card Design

We need a new business card design for a company based in Southlake, TX. We provide business consulting services in the information technology / services space. We like variations of the color blue, aqua, black, light tan, and white. Would like "cool" tones. The design should clearly communicate professionalism. Think outside the box - we don't want something "typical". Our company name is "Halvery Consulting, LLC".
Updates

Thank you all for your submissions. We have seen some very creative and inspired designs. We have made a decision and will be moving forward with that design. Appreciate all of the hard work.

Industry/Entity Type

Information Technology

Contact Information for Business Card

Megan Halvery Strube
218 West Birchfold Ridge Dr.
Southlake, TX 76418

```html
<!DOCTYPE html>
<html lang="en">
<head>
<meta charset="utf-8">
<title>Halvery Consulting, LLC — Business Card</title>
<link rel="stylesheet" href="https://fonts.googleapis.com/css2?family=Open+Sans:wght@400;600&display=swap">
<style>
  :root {
    --canvas-bg: #e9ecef;
    --card-white: #ffffff;
    --brand-blue: #3271be;
    --name-blue: #2a64b4;
    --label-blue: #7fa0cc;
    --text-dark: #2c2f33;
    --text-grey: #55595e;
    --line-white: #ffffff;
  }
  * { box-sizing: border-box; margin: 0; padding: 0; }
  html, body {
    width: 1200px;
    height: 892px;
    overflow: hidden;
  }
  body {
    background: var(--canvas-bg);
    font-family: "Open Sans", Arial, sans-serif;
    position: relative;
  }
  .card {
    position: absolute;
    left: 320px;
    width: 560px;
    height: 320px;
    box-shadow: 0 6px 18px rgba(0, 0, 0, 0.12);
  }
  .card--front { top: 96px; background: var(--card-white); }
  .card--back  { top: 476px; background: var(--brand-blue); }

  /* Front: company mark */
  .brand {
    position: absolute;
    left: 44px;
    top: 104px;
    width: 150px;
    text-align: center;
  }
  .brand__square {
    display: block;
    width: 64px;
    height: 64px;
    margin: 0 auto 10px;
    border: 1.5px solid var(--brand-blue);
  }
  .brand__name {
    font-size: 12px;
    font-weight: 400;
    letter-spacing: 0.06em;
    text-transform: uppercase;
    color: var(--brand-blue);
    line-height: 1.35;
  }

  /* Front: person + contact */
  .person {
    position: absolute;
    left: 232px;
    top: 92px;
  }
  .person__name {
    font-size: 20px;
    font-weight: 600;
    color: var(--name-blue);
    letter-spacing: 0.01em;
  }
  .person__title {
    font-size: 11.5px;
    color: var(--text-grey);
    margin-top: 2px;
  }
  .contact {
    list-style: none;
    margin-top: 30px;
  }
  .contact__item {
    display: flex;
    align-items: baseline;
    font-size: 11px;
    color: var(--text-dark);
    line-height: 1.9;
  }
  .contact__label {
    width: 22px;
    font-size: 13px;
    color: var(--label-blue);
  }
  .contact__label::after {
    content: "|";
    margin-left: 4px;
    font-size: 11px;
  }
  .contact__label { display: inline-flex; align-items: baseline; }
  .contact__value { margin-left: 4px; }

  /* Back: centred mark */
  .back-brand {
    position: absolute;
    left: 50%;
    top: 50%;
    transform: translate(-50%, -50%);
    width: 180px;
    height: 130px;
    border: 1.5px solid var(--line-white);
    display: flex;
    align-items: center;
    justify-content: center;
    text-align: center;
  }
  .back-brand__name {
    font-size: 15px;
    font-weight: 400;
    letter-spacing: 0.07em;
    text-transform: uppercase;
    color: var(--line-white);
    line-height: 1.4;
  }
</style>
</head>
<body>
  <section class="card card--front" aria-label="Business card front">
    <div class="brand">
      <span class="brand__square" aria-hidden="true"></span>
      <p class="brand__name">Halvery<br>Consulting, LLC</p>
    </div>
    <div class="person">
      <h1 class="person__name">Megan Halvery Strube</h1>
      <p class="person__title">CEO, Consultant</p>
      <ul class="contact">
        <li class="contact__item"><span class="contact__label">m</span><span class="contact__value">713-555-0142</span></li>
        <li class="contact__item"><span class="contact__label">e</span><span class="contact__value">megan.strube@halverymail.com</span></li>
        <li class="contact__item"><span class="contact__label">a</span><span class="contact__value">218 West Birchfold Ridge Dr. Southlake, TX 76418</span></li>
      </ul>
    </div>
  </section>

  <section class="card card--back" aria-label="Business card back">
    <div class="back-brand">
      <p class="back-brand__name">Halvery<br>Consulting, LLC</p>
    </div>
  </section>
</body>
</html>
```